New Business Card Design Project

I'd like a business card design around the same modern style that I used on my website www.brovanhs.com
It's gonna be one of those round corners double-sided business cards with maybe a big logo on the front and all the info on the back of the card.

Contact Information for Business Card

Marco Delgado
425-317-6084
www.brovanhs.com

www.facebook.com/BrovanHomeServices
www.intsgram.com/BrovanHomeServices

Requirements
Must have
• it needs to look elegant and modern

```html
<!DOCTYPE html>
<html lang="en">
<head>
<meta charset="utf-8">
<title>Brovan Home Services — Business Card</title>
<link href="https://fonts.googleapis.com/css2?family=Montserrat:wght@500;700;800&display=swap" rel="stylesheet">
<style>
  :root {
    --stage: #2a2a2e;
    --card-white: #ffffff;
    --navy: #16154f;
    --navy-glow: #2e2f6e;
    --brand-blue: #1a9be6;
    --ink-light: #ffffff;
    --ink-soft: #e6e7f4;
  }
  * { margin: 0; padding: 0; box-sizing: border-box; }
  html, body {
    width: 1200px; height: 800px; overflow: hidden;
    background: var(--stage);
    font-family: "Montserrat", sans-serif;
  }
  .stage {
    width: 1200px; height: 800px;
    display: flex; align-items: center; justify-content: center; gap: 40px;
  }
  .card {
    width: 540px; height: 309px; border-radius: 14px;
    position: relative; overflow: hidden;
    box-shadow: 0 18px 40px rgba(0,0,0,.45);
  }
  .card-front {
    background: var(--card-white);
    display: flex; align-items: center; justify-content: center;
  }
  .brand-lockup { display: flex; align-items: center; gap: 14px; }
  .brand-dot {
    width: 22px; height: 22px; border-radius: 50%;
    background: var(--brand-blue);
  }
  .brand-name {
    font-weight: 800; font-size: 38px; color: var(--brand-blue);
    letter-spacing: -0.5px; line-height: 1;
  }
  .card-back { background: var(--navy); color: var(--ink-light); }
  .sparkle-field {
    position: absolute; top: 0; right: 0; width: 62%; height: 62%;
    background: radial-gradient(ellipse at 65% 35%, var(--navy-glow) 0%, rgba(46,47,110,.45) 45%, rgba(22,21,79,0) 75%);
  }
  .contact-block { position: absolute; left: 38px; bottom: 34px; }
  .contact-name {
    font-weight: 700; font-size: 24px; letter-spacing: .3px;
    padding-bottom: 8px; margin-bottom: 10px;
    border-bottom: 1.5px solid var(--ink-soft);
    width: 280px;
  }
  .contact-list { list-style: none; }
  .contact-item {
    display: flex; align-items: center; gap: 9px;
    font-weight: 500; font-size: 13.5px; color: var(--ink-soft);
    line-height: 1; margin-bottom: 6px;
  }
  .contact-icon {
    width: 17px; height: 17px; border-radius: 4px;
    background: var(--ink-light); flex: none;
    display: flex; align-items: center; justify-content: center;
  }
  .contact-icon svg { width: 11px; height: 11px; }
</style>
</head>
<body>
<main class="stage">
  <section class="card card-front" aria-label="Card front">
    <div class="brand-lockup">
      <span class="brand-dot"></span>
      <span class="brand-name">Brovan Home Services</span>
    </div>
  </section>

  <section class="card card-back" aria-label="Card back">
    <div class="sparkle-field" role="img" aria-label="Faint sparkle pattern decoration"></div>
    <div class="contact-block">
      <h1 class="contact-name">Marco Delgado</h1>
      <ul class="contact-list">
        <li class="contact-item">
          <span class="contact-icon">
            <svg viewBox="0 0 24 24"><path fill="#16154f" d="M6.6 10.8a15 15 0 0 0 6.6 6.6l2.2-2.2c.3-.3.7-.4 1-.2 1.1.4 2.3.6 3.6.6.6 0 1 .4 1 1V20c0 .6-.4 1-1 1A17 17 0 0 1 3 4c0-.6.4-1 1-1h3.5c.6 0 1 .4 1 1 0 1.3.2 2.5.6 3.6.1.3 0 .7-.2 1z"/></svg>
          </span>425-317-6084
        </li>
        <li class="contact-item">
          <span class="contact-icon">
            <svg viewBox="0 0 24 24" fill="none" stroke="#16154f" stroke-width="2.2"><circle cx="12" cy="12" r="9"/><path d="M3 12h18M12 3c3 3 3 15 0 18M12 3c-3 3-3 15 0 18"/></svg>
          </span>www.brovanhs.com
        </li>
        <li class="contact-item">
          <span class="contact-icon"></span>BrovanHomeServices
        </li>
        <li class="contact-item">
          <span class="contact-icon"></span>BrovanHomeServices
        </li>
      </ul>
    </div>
  </section>
</main>
</body>
</html>
```